Design a "healthy, happy dog and cat" cheque/check background

I am looking for a few design concepts featuring a happy healthy dog and cat, that will be used as the background of a paper cheque/check.

This will require Photoshop and stock photos.

Here is the design brief: https://docs.plinvaro.com/document/d/4Rt8mKx2LqW9zVbN3cHy7TfJ1sDp6GaE0uYoZiXeMwnB/edit?usp=sharing

Colors

Designer to choose colors to be used in the design.

Requirements
Must have
• A happy dog and cat the main focus within the "empty" central part of the cheque/check, and a complementary background for the rest of the cheque, following the design guidelines in the attached plinvaro doc.

```html
<!DOCTYPE html>
<html lang="en">
<head>
<meta charset="utf-8">
<title>Personal Cheque – Pets Background</title>
<link href="https://fonts.googleapis.com/css2?family=Arimo:wght@400;700&family=Share+Tech+Mono&display=swap" rel="stylesheet">
<style>
  :root {
    --page: #ffffff;
    --grass-light: #dfeccf;
    --grass-mid: #c9e0b0;
    --grass-deep: #b3d195;
    --fur-soft: #e6e1d8;
    --ink: #2b2b2b;
    --ink-soft: #444444;
    --rule: #3a3a3a;
    --field: #ffffff;
  }
  html, body {
    margin: 0;
    padding: 0;
    width: 1200px;
    height: 544px;
    overflow: hidden;
    background: var(--page);
    font-family: "Arimo", Arial, sans-serif;
    color: var(--ink);
  }
  .canvas {
    position: relative;
    width: 1200px;
    height: 544px;
    background: var(--page);
  }
  .cheque {
    position: absolute;
    left: 24px;
    top: 20px;
    width: 1168px;
    height: 388px;
    overflow: hidden;
  }
  .cheque__photo {
    position: absolute;
    inset: 0;
    background:
      radial-gradient(ellipse 38% 55% at 52% 58%, var(--fur-soft) 0%, rgba(230,225,216,0) 100%),
      linear-gradient(180deg, var(--grass-light) 0%, var(--grass-mid) 60%, var(--grass-deep) 100%);
  }
  .text { position: absolute; margin: 0; white-space: nowrap; line-height: 1; }

  .account-holder { left: 34px; top: 60px; font-size: 21px; font-weight: 700; color: var(--ink-soft); }
  .account-address { left: 34px; top: 79px; font-size: 19px; line-height: 23px; color: var(--ink-soft); white-space: pre; }
  .cheque-number { left: 1000px; top: 41px; font-size: 23px; font-weight: 700; color: #111; }

  .date-label { left: 759px; top: 103px; font-size: 19px; color: var(--ink); }
  .date-boxes { position: absolute; left: 824px; top: 70px; display: flex; gap: 5px; }
  .date-box { width: 35px; height: 36px; background: var(--field); display: flex; justify-content: center; }
  .date-box span { margin-top: 46px; font-size: 13px; color: var(--ink-soft); }

  .pay-label { left: 32px; top: 170px; font-size: 14px; line-height: 14px; color: var(--ink); }
  .dollar-sign { left: 924px; top: 182px; font-size: 29px; color: var(--ink); }
  .amount-box { position: absolute; left: 948px; top: 154px; width: 194px; height: 48px; background: var(--field); }
  .amount-words { left: 894px; top: 247px; font-size: 14px; color: var(--ink); }

  .bank-mark { position: absolute; left: 40px; top: 276px; width: 64px; height: 64px; background: var(--ink); }
  .bank-name { left: 130px; top: 290px; font-size: 18px; font-weight: 700; color: #111; }
  .bank-address { left: 130px; top: 310px; font-size: 17px; line-height: 20px; color: #111; white-space: pre; }
  .company-name { left: 786px; top: 326px; font-size: 14px; color: #111; }
  .memo-label { left: 36px; top: 378px; font-size: 11px; color: var(--ink); }

  .security-badge { position: absolute; left: 1138px; top: 252px; width: 26px; height: 132px; border: 1.5px solid #666; border-radius: 3px; background: rgba(255,255,255,0.35); }

  .cheque__rules { position: absolute; inset: 0; }

  .micr-line {
    position: absolute;
    left: 54px;
    top: 450px;
    margin: 0;
    font-family: "Share Tech Mono", "Courier New", monospace;
    font-size: 27px;
    letter-spacing: 2px;
    color: #111;
    white-space: pre;
  }
</style>
</head>
<body>
<main class="canvas">
  <section class="cheque">
    <div class="cheque__photo" role="img" aria-label="Photograph of a row of young kittens sitting on green grass"></div>

    <svg class="cheque__rules" width="1168" height="388" viewBox="0 0 1168 388" aria-hidden="true">
      <g fill="none" stroke="var(--rule)" stroke-width="1.3">
        <polyline points="32,202 900,202 900,182"/>
        <polyline points="32,256 880,256 888,220"/>
        <line x1="36" y1="377" x2="564" y2="377"/>
        <line x1="662" y1="377" x2="1076" y2="377"/>
      </g>
    </svg>

    <p class="text account-holder">Northvale Cheques Personal Cheque</p>
    <p class="text account-address">15 Residential Street
Toronto, Ontario M1M 1M1</p>
    <p class="text cheque-number">101</p>

    <p class="text date-label">DATE</p>
    <div class="date-boxes">
      <div class="date-box"><span>D</span></div>
      <div class="date-box"><span>D</span></div>
      <div class="date-box"><span>M</span></div>
      <div class="date-box"><span>M</span></div>
      <div class="date-box"><span>Y</span></div>
      <div class="date-box"><span>Y</span></div>
      <div class="date-box"><span>Y</span></div>
      <div class="date-box"><span>Y</span></div>
    </div>

    <p class="text pay-label">PAY TO THE<br>ORDER OF</p>
    <p class="text dollar-sign">$</p>
    <div class="amount-box"></div>
    <p class="text amount-words">100 DOLLARS</p>

    <div class="bank-mark"></div>
    <p class="text bank-name">Your Financial Institution</p>
    <p class="text bank-address">200 Finance Avenue
Your City, Your Province A1B 2CS</p>
    <p class="text company-name">Optional Company Name</p>
    <p class="text memo-label">MEMO</p>

    <div class="security-badge"></div>
  </section>

  <p class="micr-line">⑈101⑈  ⑆12345⑉678⑆  12345⑉6789⑈</p>
</main>
</body>
</html>
```